Website for software company "velora"

We need a website for our software company/startup named "velora". We are developing several products (currently 3 standard-software products) which are all in different sectors, but all our products are available for Laptops/PC/Mobile Phones/Tablets, ... We do also create custom software and support our customers with consulting to optimize their processes.
We already have a Logo which you can find in the attached files.
We are a young team of 4 members (two founders and 2 employees).

To get an idea of our products -> the first one is a planning software for healthcare organizations (eg. BlueHaven, firebrigade, pharmacy), the second one is a booking software for sport clubs and the third one is a competition software for sports hunting. You see very diverse. Include or ignore this info of our products as you like.

The design has to be a bootstrap 4 (or higher) design. We have licenced FontAwesome as iconset. Responsive design should come without saying.

• Starting page, product pages, news section, contact, team, services

```html
<!DOCTYPE html>
<html lang="en">
<head>
<meta charset="utf-8">
<title>Velora — Software Development</title>
<link rel="stylesheet" href="https://fonts.googleapis.com/css2?family=Montserrat:ital,wght@0,400;0,500;0,600;0,700;1,400&family=Playfair+Display:wght@400;700&display=swap">
<style>
:root{
  --orange:#f0801f;
  --orange-deep:#e9650f;
  --ink:#2b2b2b;
  --text:#555;
  --muted:#8a8a8a;
  --line:#e6e6e6;
  --footer:#262a31;
  --white:#fff;
}
*{box-sizing:border-box;margin:0;padding:0}
html,body{width:1200px;height:3831px;overflow:hidden}
body{position:relative;font-family:'Montserrat',sans-serif;color:var(--ink);background:var(--white)}
.abs{position:absolute}
.serif{font-family:'Playfair Display',serif;font-weight:400}
.eyebrow{color:var(--orange);font-size:12px;font-weight:600;letter-spacing:1px;text-transform:uppercase;text-align:center}
.section-title{font-family:'Playfair Display',serif;font-weight:400;font-size:31px;color:var(--ink);white-space:nowrap;line-height:40px}
.section-title::after{content:"";display:inline-block;width:62px;height:1px;background:var(--orange);margin-left:8px;vertical-align:-2px}
.btn{position:absolute;background:var(--orange);color:#fff;font-size:11px;font-weight:600;text-transform:uppercase;display:flex;align-items:center;justify-content:center;letter-spacing:.3px;box-shadow:0 3px 8px rgba(240,128,31,.3)}

/* header */
.site-header{position:absolute;top:0;left:0;width:1200px;height:67px;background:#fff}
.brand{position:absolute;top:13px;left:119px;font-family:'Montserrat',sans-serif;font-weight:600;font-size:38px;letter-spacing:1px;color:var(--ink);line-height:40px}
.nav a{position:absolute;top:27px;font-size:11px;font-weight:500;color:var(--ink);text-decoration:none;text-transform:uppercase}
.nav .phone{font-size:10px;font-weight:600}

/* hero */
.hero{position:absolute;top:67px;left:0;width:1200px;height:701px;overflow:hidden}
.hero-photo{position:absolute;inset:0;background:linear-gradient(180deg,#e9e4df 0%,#f5f2ef 40%,#dcd9d6 75%,#ecebea 100%)}
.hero-title{position:absolute;top:140px;width:1200px;text-align:center;font-size:47px;color:var(--ink)}
.product-card{position:absolute;background:var(--orange);color:#fff;text-align:center;padding-top:38px}
.product-card h3{font-family:'Playfair Display',serif;font-weight:700;font-size:14px;text-transform:uppercase;margin-top:14px}
.product-card p{font-size:11px;line-height:18px;margin-top:10px}
.product-card.featured{background:#fff;color:var(--text);box-shadow:0 4px 14px rgba(0,0,0,.12)}
.product-card.featured h3{color:var(--orange)}

/* about */
.about-media{position:absolute;left:174px;top:774px;width:341px;height:450px;background:#ebebeb}
.about-title{position:absolute;left:595px;top:840px;font-size:31px}
.about-lead{position:absolute;left:595px;top:890px;width:395px;font-size:13px;line-height:24px;color:var(--ink)}
.about-body{position:absolute;left:595px;top:955px;width:380px;font-size:11.5px;line-height:22px;color:var(--text)}

/* services */
.service{position:absolute;width:230px;text-align:center}
.service svg{display:block;margin:0 auto}
.service span{display:block;margin-top:8px;font-size:12.5px;font-weight:500;line-height:16px;color:var(--ink)}

/* expertise */
.tech{position:absolute;width:135px;height:77px;background:#fff;box-shadow:0 2px 6px rgba(0,0,0,.12);display:flex;align-items:center;justify-content:center;font-size:15px;font-weight:600;color:#3a3a3a}

/* team */
.member{position:absolute;top:2207px;width:223px;height:262px;overflow:hidden}
.member-photo{position:absolute;inset:0;background:linear-gradient(180deg,#bdbdbd 0%,#8e8e8e 55%,#3c3c3c 100%)}
.member span{position:absolute;bottom:22px;width:100%;text-align:center;font-size:19px;color:var(--orange)}

/* testimonial */
.testimonial{position:absolute;top:2508px;left:0;width:1200px;height:463px;background:linear-gradient(100deg,var(--orange-deep) 0%,#f28a1a 50%,var(--orange-deep) 100%)}
.testimonial .section-title{color:#fff}
.testimonial .section-title::after{background:#fff}
.quote-card{position:absolute;left:189px;top:116px;width:815px;height:274px;background:#fff;border-radius:6px;box-shadow:0 10px 0 -2px rgba(255,255,255,.55)}
.quote-text{position:absolute;left:113px;top:58px;width:640px;font-style:italic;font-size:17px;line-height:30px;color:#555}
.arrow-btn{position:absolute;top:218px;width:44px;height:44px;border-radius:50%;background:rgba(255,255,255,.35);border:1px solid rgba(255,255,255,.6);display:flex;align-items:center;justify-content:center;color:#fff;font-size:18px}

/* call */
.call-photo{position:absolute;top:3140px;left:0;width:1200px;height:333px;background:linear-gradient(180deg,#fff 0%,#d6dbe0 25%,#8f97a0 60%,#59626c 100%)}

/* footer */
.site-footer{position:absolute;top:3473px;left:0;width:1200px;height:358px;background:var(--footer);color:#d8d8d8}
.site-footer h4{position:absolute;top:73px;font-size:16px;font-weight:600;color:#fff}
.site-footer .link{position:absolute;left:561px;font-size:12px;color:#cfcfcf}
.site-footer .info{position:absolute;left:819px;font-size:12px;line-height:20px;color:#cfcfcf}
.social{position:absolute;top:183px;width:26px;height:26px;border:1.5px solid var(--orange);border-radius:50%}
</style>
</head>
<body>

<header class="site-header">
  <div class="brand">VELORA</div>
  <nav class="nav">
    <a style="left:534px">Home</a>
    <a style="left:619px">Product</a>
    <a style="left:730px">News</a>
    <a style="left:814px">Contact</a>
    <a style="left:922px">Team</a>
    <svg class="abs" style="left:982px;top:25px" width="16" height="16" viewBox="0 0 24 24" fill="none" stroke="#999" stroke-width="1.6"><path d="M5 3h4l2 5-3 2a12 12 0 0 0 6 6l2-3 5 2v4a2 2 0 0 1-2 2A17 17 0 0 1 3 5a2 2 0 0 1 2-2z"/></svg>
    <a class="phone" style="left:1008px;top:27px">123.456.7890</a>
  </nav>
</header>

<section class="hero">
  <div class="hero-photo" role="img" aria-label="Bright office desk with laptop, notebooks and a potted plant"></div>
  <p class="eyebrow abs" style="top:117px;width:1200px;letter-spacing:1.2px">Life cycle stage of custom</p>
  <h1 class="hero-title serif">Software Development</h1>

  <div class="product-card" style="left:248px;top:269px;width:235px;height:187px">
    <svg width="40" height="40" viewBox="0 0 40 40" fill="none" stroke="#fff" stroke-width="2"><rect x="4" y="4" width="32" height="32" rx="4"/><line x1="4" y1="12" x2="36" y2="12"/><circle cx="20" cy="24" r="6"/><circle cx="20" cy="24" r="2"/></svg>
    <h3>Planning Software</h3>
    <p>Vel Illum Dolore Eu Feugiat<br>Nulla Facilisis At Vero Eros Et</p>
  </div>
  <div class="product-card featured" style="left:483px;top:255px;width:234px;height:216px;padding-top:52px">
    <svg width="40" height="40" viewBox="0 0 40 40" fill="none" stroke="#f0801f" stroke-width="2"><rect x="4" y="6" width="32" height="22" rx="2"/><line x1="14" y1="34" x2="26" y2="34"/><line x1="20" y1="28" x2="20" y2="34"/><rect x="9" y="11" width="8" height="6"/><line x1="21" y1="12" x2="31" y2="12"/><line x1="21" y1="17" x2="31" y2="17"/><line x1="9" y1="22" x2="31" y2="22"/></svg>
    <h3>Booking Software</h3>
    <p>Vel Illum Dolore Eu Feugiat<br>Nulla Facilisis At Vero Eros Et</p>
  </div>
  <div class="product-card" style="left:717px;top:269px;width:233px;height:187px">
    <svg width="40" height="40" viewBox="0 0 40 40" fill="none" stroke="#fff" stroke-width="2"><rect x="4" y="4" width="26" height="22" rx="2"/><path d="M11 13l6-4 6 4v6l-6 3-6-3z"/><circle cx="30" cy="30" r="6"/><line x1="10" y1="32" x2="22" y2="32"/></svg>
    <h3>Competition Software</h3>
    <p>Vel Illum Dolore Eu Feugiat<br>Nulla Facilisis At Vero Eros Et</p>
  </div>

  <svg class="abs" style="left:0;top:0" width="1200" height="701" viewBox="0 0 1200 701">
    <polygon points="0,550 600,668 1200,550 1200,701 0,701" fill="#fff"/>
    <polygon points="0,550 600,640 1200,550 1200,558 600,668 0,562" fill="#f0801f"/>
  </svg>
</section>

<section>
  <div class="about-media">
    <svg class="abs" style="left:0;top:0" width="341" height="450" viewBox="0 0 341 450">
      <polygon points="0,20 275,233 0,432" fill="#3d5f8f" role="img" aria-label="Developer monitor showing code"/>
      <polygon points="0,0 275,233 0,20" fill="#fff"/>
      <polygon points="0,432 275,233 0,450" fill="#fff"/>
    </svg>
  </div>
  <h2 class="about-title serif">About Us</h2>
  <p class="about-lead">Lorem ipsum dolor sit amet, consectetuer adipiscing elit, sed diam nonummy nibh euismod tincidunt ut .</p>
  <p class="about-body">Ut wisi enim ad minim veniam, quis nostrud exerci tation suscipit lobortis nisl ut aliquip ex ea commodo consequat. Duis autem vel eum iriure dolor in hendrerit in velit esse molestie consequatvel illum dolore eu</p>
  <div class="btn" style="left:597px;top:1085px;width:195px;height:45px">Contact Us Today</div>
</section>

<section>
  <h2 class="section-title abs" style="left:512px;top:1258px">Services</h2>

  <div class="service" style="left:236px;top:1330px">
    <svg width="116" height="116" viewBox="0 0 116 116" fill="none"><circle cx="58" cy="58" r="56" stroke="#f0801f" stroke-width="1.5"/><circle cx="58" cy="58" r="49" stroke="#f0801f" stroke-width="1.5"/><rect x="38" y="38" width="40" height="30" rx="3" stroke="#2b2b2b" stroke-width="3"/><circle cx="58" cy="50" r="6" fill="#2b2b2b"/><line x1="50" y1="76" x2="66" y2="76" stroke="#2b2b2b" stroke-width="3"/></svg>
    <span>Software Consulting</span>
  </div>
  <div class="service" style="left:487px;top:1330px">
    <svg width="116" height="116" viewBox="0 0 116 116" fill="none"><circle cx="58" cy="58" r="56" stroke="#f0801f" stroke-width="1.5"/><circle cx="58" cy="58" r="49" stroke="#f0801f" stroke-width="1.5"/><rect x="36" y="38" width="36" height="28" stroke="#2b2b2b" stroke-width="3"/><line x1="44" y1="46" x2="62" y2="46" stroke="#2b2b2b" stroke-width="3"/><line x1="44" y1="54" x2="58" y2="54" stroke="#2b2b2b" stroke-width="3"/><rect x="70" y="52" width="10" height="20" fill="#2b2b2b"/></svg>
    <span>Software Development<br>Outsourcing</span>
  </div>
  <div class="service" style="left:738px;top:1330px">
    <svg width="116" height="116" viewBox="0 0 116 116" fill="none"><circle cx="58" cy="58" r="56" stroke="#f0801f" stroke-width="1.5"/><circle cx="58" cy="58" r="49" stroke="#f0801f" stroke-width="1.5"/><circle cx="58" cy="40" r="5" fill="#2b2b2b"/><circle cx="42" cy="72" r="5" fill="#2b2b2b"/><circle cx="58" cy="72" r="5" fill="#2b2b2b"/><circle cx="74" cy="72" r="5" fill="#2b2b2b"/><path d="M58 46v12M42 66v-8h32v8M58 58v8" stroke="#2b2b2b" stroke-width="3"/></svg>
    <span>Team Augmentation</span>
  </div>
  <div class="service" style="left:236px;top:1510px">
    <svg width="116" height="116" viewBox="0 0 116 116" fill="none"><circle cx="58" cy="58" r="56" stroke="#f0801f" stroke-width="1.5"/><circle cx="58" cy="58" r="49" stroke="#f0801f" stroke-width="1.5"/><ellipse cx="58" cy="60" rx="10" ry="16" stroke="#2b2b2b" stroke-width="3"/><path d="M48 54h-10M48 64h-10M68 54h10M68 64h10M58 44v-6" stroke="#2b2b2b" stroke-width="3"/></svg>
    <span>Legacy Software<br>Modernization</span>
  </div>
  <div class="service" style="left:487px;top:1510px">
    <svg width="116" height="116" viewBox="0 0 116 116" fill="none"><circle cx="58" cy="58" r="56" stroke="#f0801f" stroke-width="1.5"/><circle cx="58" cy="58" r="49" stroke="#f0801f" stroke-width="1.5"/><rect x="38" y="38" width="40" height="30" stroke="#2b2b2b" stroke-width="3"/><path d="M52 48l-5 5 5 5M64 48l5 5-5 5" stroke="#2b2b2b" stroke-width="3"/><line x1="50" y1="76" x2="66" y2="76" stroke="#2b2b2b" stroke-width="3"/></svg>
    <span>Custom Software<br>Development</span>
  </div>
  <div class="service" style="left:738px;top:1510px">
    <svg width="116" height="116" viewBox="0 0 116 116" fill="none"><circle cx="58" cy="58" r="56" stroke="#f0801f" stroke-width="1.5"/><circle cx="58" cy="58" r="49" stroke="#f0801f" stroke-width="1.5"/><rect x="40" y="42" width="36" height="26" stroke="#2b2b2b" stroke-width="3"/><rect x="50" y="36" width="16" height="20" fill="#fff" stroke="#2b2b2b" stroke-width="3"/><line x1="48" y1="76" x2="68" y2="76" stroke="#2b2b2b" stroke-width="3"/></svg>
    <span>Software Product<br>Development</span>
  </div>

  <div class="btn" style="left:514px;top:1700px;width:180px;height:44px">View All Services</div>
</section>

<div class="abs" style="left:0;top:1806px;width:1200px;height:1px;background:var(--line)"></div>

<section>
  <p class="eyebrow abs" style="left:0;top:1844px;width:1200px;letter-spacing:3px">Expertise in</p>
  <h2 class="section-title abs" style="left:364px;top:1864px">Delivering The Right Solution</h2>

  <div class="tech" style="left:232px;top:1940px">Serpent</div>
  <div class="tech" style="left:382px;top:1940px">Streamly</div>
  <div class="tech" style="left:532px;top:1940px">Nodra</div>
  <div class="tech" style="left:682px;top:1940px">Scriptor</div>
  <div class="tech" style="left:831px;top:1940px">Typeon</div>
  <div class="tech" style="left:232px;top:2030px">Vista</div>
  <div class="tech" style="left:382px;top:2030px">Orbit</div>
  <div class="tech" style="left:532px;top:2030px">Flitter</div>
  <div class="tech" style="left:682px;top:2030px">Droidix</div>
  <div class="tech" style="left:831px;top:2030px">Orchard</div>
</section>

<section>
  <h2 class="section-title abs" style="left:458px;top:2137px">Meet Our Team</h2>
  <div class="member" style="left:120px"><div class="member-photo" role="img" aria-label="Black and white portrait of team member"></div><span>Mara Lind</span></div>
  <div class="member" style="left:366px"><div class="member-photo" role="img" aria-label="Black and white portrait of team member"></div><span>Tomas Reyl</span></div>
  <div class="member" style="left:611px"><div class="member-photo" role="img" aria-label="Black and white portrait of team member"></div><span>Ines Varo</span></div>
  <div class="member" style="left:856px"><div class="member-photo" role="img" aria-label="Black and white portrait of team member"></div><span>Jonah Pell</span></div>
</section>

<section class="testimonial">
  <h2 class="section-title abs" style="left:474px;top:46px">Testimonial</h2>
  <div class="arrow-btn" style="left:120px">&larr;</div>
  <div class="arrow-btn" style="left:1035px">&rarr;</div>
  <div class="quote-card">
    <span class="abs serif" style="left:40px;top:28px;font-size:90px;line-height:90px;color:var(--orange)">&ldquo;</span>
    <p class="quote-text">Dolore magna aliquam erat volutpat. Ut wisi enim ad minim veniam, qu nostrud exerci tation ullamcorper suscipit lobortis nisl ut&nbsp; vel illum dolore eu feugiat nulla facilisis at vero eros et accumsan et iusto odio dignissim qui</p>
    <div class="abs" role="img" aria-label="Client avatar" style="left:42px;top:196px;width:42px;height:42px;border-radius:50%;background:linear-gradient(135deg,#c9b6a4,#6f5a4a)"></div>
    <span class="abs" style="left:113px;top:208px;font-size:14px;color:var(--ink)">Leon Farrow</span>
  </div>
</section>

<section>
  <h2 class="section-title abs" style="left:507px;top:3047px">Call Us Today</h2>
  <p class="eyebrow abs" style="left:0;top:3110px;width:1200px">Ready to build your custom software ?</p>
  <div class="call-photo" role="img" aria-label="Busy open-plan office with people working at desks"></div>
  <div class="abs" style="left:406px;top:3153px;width:44px;height:44px;border-radius:50%;background:#f29a52;display:flex;align-items:center;justify-content:center">
    <svg width="20" height="20" viewBox="0 0 24 24" fill="none" stroke="#fff" stroke-width="2"><path d="M5 3h4l2 5-3 2a12 12 0 0 0 6 6l2-3 5 2v4a2 2 0 0 1-2 2A17 17 0 0 1 3 5a2 2 0 0 1 2-2z"/></svg>
  </div>
  <span class="abs" style="left:467px;top:3162px;font-size:22px;font-weight:500;color:var(--ink)">123.456.7890</span>
  <div class="btn" style="left:690px;top:3153px;width:99px;height:44px;font-size:10px">Let's Talk</div>
</section>

<footer class="site-footer">
  <div class="abs" style="left:210px;top:116px;font-weight:600;font-size:40px;letter-spacing:1px;color:#fff;line-height:44px">VELORA</div>
  <div class="social" style="left:261px" aria-label="Social link"></div>
  <div class="social" style="left:297px" aria-label="Social link"></div>
  <div class="social" style="left:333px" aria-label="Social link"></div>

  <h4 style="left:550px">Quick Link</h4>
  <span class="link" style="top:121px">Home</span>
  <span class="link" style="top:147px">Product</span>
  <span class="link" style="top:174px">Team</span>
  <span class="link" style="top:200px">News</span>
  <span class="link" style="top:226px">Contact</span>

  <h4 style="left:782px">Contact Info</h4>
  <svg class="abs" style="left:780px;top:120px" width="18" height="22" viewBox="0 0 18 22" fill="none" stroke="#f0801f" stroke-width="1.6"><path d="M9 21s7-7 7-12A7 7 0 0 0 2 9c0 5 7 12 7 12z"/><circle cx="9" cy="9" r="2.5"/></svg>
  <span class="info" style="top:117px">Address Lorem ipsum 2360<br>3rd Street Location, AB 91407</span>
  <svg class="abs" style="left:780px;top:180px" width="18" height="18" viewBox="0 0 24 24" fill="none" stroke="#f0801f" stroke-width="1.8"><path d="M5 3h4l2 5-3 2a12 12 0 0 0 6 6l2-3 5 2v4a2 2 0 0 1-2 2A17 17 0 0 1 3 5a2 2 0 0 1 2-2z"/></svg>
  <span class="info" style="top:178px">123.456.7890</span>
  <svg class="abs" style="left:780px;top:226px" width="18" height="14" viewBox="0 0 18 14" fill="none" stroke="#f0801f" stroke-width="1.6"><rect x="1" y="1" width="16" height="12"/><path d="M1 1l8 7 8-7"/></svg>
  <span class="info" style="top:223px">info@velora.com</span>

  <div class="abs" style="left:0;top:302px;width:1200px;height:1px;background:#3a3f47"></div>
  <p class="abs" style="left:0;top:326px;width:1200px;text-align:center;font-size:10px;color:#cfcfcf">© 2022 Velora. All right reserved.</p>
</footer>

</body>
</html>
```